BrivoTerna. Lantern of the Steady Harvest. Business card

Professional business card for BrivoTerna (Lantern of the Steady Harvest)
My rationale: Strategy-> Execution-> Results-> Value that lead to the BrivoTerna name: We put the Lantern of the Steady Harvest.
We deliver value to our customers helping them at defining a good strategy (cyan arrow). 90% of well formulated strategies fail due to poor execution so we also consider strategical execution very important (green arrow). Due to the execution we obtain the results (blue arrow). Finally, the results provide feedback to redefine strategy, and the new strategy has to be executed and new results obtained providing new feedback and on and on. It's like a wheel that finally, must create corporate value: value for shareholders, staholders, employees, providers...-

Target Market(s)

CEOs and steering comitees , invewrnent funds

Industry/Entity Type

Business Consultant

Contact Information for Business Card

Teodoro Vinsquel
CEO & Founder
teodoro.vinsquel@brivoterna-example.com
Mobile: +34 655.803.912
www.brivoterna-example.com

Colors

Designer to choose colors to be used in the design.

Requirements
Nice to have
• Nice to hace the words: Strategy, execution, results
• Nice to vave the claim: Lantern of the Steady Harvest
• The three colors should be shown:
• cyan for STRATEGY
• green for EXECUTION
• blue for RESULTS
Should not have
• Complete black background

```html
<!DOCTYPE html>
<html lang="en">
<head>
<meta charset="utf-8">
<title>BrivoTerna – Business Card</title>
<link href="https://fonts.googleapis.com/css2?family=Roboto:wght@400;500;700&display=swap" rel="stylesheet">
<style>
  :root {
    --backdrop: #b5b5b5;
    --card: #f7f7f7;
    --results-blue: #0b2d8f;
    --execution-green: #8cc43c;
    --strategy-cyan: #00a9e6;
    --ink: #3a3a3a;
  }
  * { margin: 0; padding: 0; box-sizing: border-box; }
  html, body {
    width: 1200px; height: 750px; overflow: hidden;
    background: var(--backdrop);
    font-family: "Roboto", Arial, sans-serif;
  }
  .card {
    position: absolute;
    top: 230px;
    width: 494px; height: 282px;
    background: var(--card);
  }
  .card--front { left: 89px; }
  .card--back { left: 620px; }

  .holder-name {
    position: absolute; left: 37px; top: 28px;
    font-size: 20px; font-weight: 500;
    color: var(--results-blue);
  }
  .holder-role {
    position: absolute; left: 37px; top: 55px;
    font-size: 15.5px; font-weight: 400;
    color: var(--execution-green);
  }
  .flow-arrow {
    position: absolute; left: 0;
    width: 276px; height: 16px;
  }
  .flow-arrow--results { top: 90px; }
  .flow-arrow--execution { top: 175px; }
  .flow-arrow--strategy { top: 239px; }

  .contact {
    position: absolute; left: 37px;
    font-size: 12.5px; line-height: 17px;
    color: var(--ink);
  }
  .contact--direct { top: 124px; }
  .contact--web { top: 204px; }

  .brand-name {
    position: absolute; left: 0; right: 0; top: 118px;
    text-align: center;
    font-size: 44px; font-weight: 700;
    letter-spacing: -1px;
    color: var(--results-blue);
  }
</style>
</head>
<body>
  <section class="card card--front">
    <h1 class="holder-name">Teodoro Vinsquel</h1>
    <p class="holder-role">CEO &amp; Founder</p>

    <svg class="flow-arrow flow-arrow--results" viewBox="0 0 276 16" aria-hidden="true">
      <rect x="0" y="6.5" width="264" height="3" fill="var(--results-blue)"/>
      <polygon points="263,0 276,8 263,16" fill="var(--results-blue)"/>
    </svg>

    <p class="contact contact--direct">+34 655.803.912<br>teodoro.vinsquel@brivoterna-example.com</p>

    <svg class="flow-arrow flow-arrow--execution" viewBox="0 0 276 16" aria-hidden="true">
      <rect x="0" y="6.5" width="264" height="3" fill="var(--execution-green)"/>
      <polygon points="263,0 276,8 263,16" fill="var(--execution-green)"/>
    </svg>

    <p class="contact contact--web">www.brivoterna-example.com</p>

    <svg class="flow-arrow flow-arrow--strategy" viewBox="0 0 276 16" aria-hidden="true">
      <rect x="0" y="6.5" width="264" height="3" fill="var(--strategy-cyan)"/>
      <polygon points="263,0 276,8 263,16" fill="var(--strategy-cyan)"/>
    </svg>
  </section>

  <section class="card card--back">
    <p class="brand-name">BrivoTerna</p>
  </section>
</body>
</html>
```